Upmarket Dessert Lounge needs a Business Card Design

We are an upmarket dessert lounge needing a business card to match our image.

We want something that is simple yet beautiful, feminine, classy, sophisticated and elegant. We want it to stand out and don't mind if it is bold.

The design should include our logo and colours of red or maroon with gold highlights. We don't mind if black is used.

Marlow & Quince

Target Market(s)

For those who like to indulge or treat themselves and give in to their temptations on good quality desserts.

Industry/Entity Type

Business

Requirements
Must have
• Must include our logo and our name

Marlow & Quince

M & Q

```html
<!DOCTYPE html>
<html lang="en">
<head>
<meta charset="utf-8">
<title>Marlow &amp; Quince — Business Card</title>
<link href="https://fonts.googleapis.com/css2?family=Open+Sans:wght@400;600;700&display=swap" rel="stylesheet">
<style>
  :root {
    --maroon: #7a1719;
    --peach: #fdd29c;
    --peach-line: #f6c88e;
    --white: #ffffff;
    --ink: #3d3d3d;
    --backdrop: #8a5a3c;
  }
  html, body {
    margin: 0;
    padding: 0;
    overflow: hidden;
  }
  .canvas {
    position: relative;
    width: 1200px;
    height: 402px;
    background: var(--backdrop);
    overflow: hidden;
    font-family: "Open Sans", sans-serif;
  }
  .card {
    position: absolute;
    width: 511px;
    height: 291px;
    box-shadow: 0 2px 6px rgba(0,0,0,.35);
    overflow: hidden;
  }
  .card--front {
    left: 66px;
    top: 57px;
    background: var(--white);
  }
  .card--back {
    left: 628px;
    top: 51px;
    background: var(--peach);
  }
  .card__swoosh {
    position: absolute;
    inset: 0;
  }
  .brand-name {
    position: absolute;
    left: 148px;
    top: 100px;
    transform: translate(-50%, -50%);
    margin: 0;
    color: var(--maroon);
    font-weight: 600;
    font-size: 25px;
    letter-spacing: 1px;
    white-space: nowrap;
  }
  .monogram {
    position: absolute;
    left: 50%;
    top: 50%;
    transform: translate(-50%, -50%);
    margin: 0;
    color: var(--maroon);
    font-weight: 600;
    font-size: 92px;
    line-height: 1;
    white-space: nowrap;
  }
  .person {
    position: absolute;
    left: 273px;
    top: 170px;
    margin: 0;
    padding-bottom: 3px;
    border-bottom: 2px solid var(--peach-line);
    color: var(--maroon);
    font-size: 16px;
    font-weight: 700;
    white-space: nowrap;
  }
  .person__title {
    font-weight: 400;
    font-size: 13px;
  }
  .address {
    position: absolute;
    right: 262px;
    top: 201px;
    margin: 0;
    text-align: right;
    font-style: normal;
    color: var(--ink);
    font-size: 12.5px;
    line-height: 16.5px;
  }
  .contacts {
    position: absolute;
    left: 273px;
    top: 201px;
    margin: 0;
    padding: 0;
    list-style: none;
    color: var(--ink);
    font-size: 12.5px;
    line-height: 17.5px;
  }
  .contacts li {
    display: flex;
    align-items: center;
    gap: 5px;
  }
  .contacts svg {
    width: 10px;
    height: 10px;
    flex: none;
  }
</style>
</head>
<body>
<div class="canvas">

  <section class="card card--front">
    <svg class="card__swoosh" viewBox="0 0 511 291" aria-hidden="true">
      <path d="M300 0 Q440 20 511 80 L511 0 Z" fill="var(--peach)"/>
      <path d="M300 0 Q440 20 511 80" fill="none" stroke="var(--maroon)" stroke-width="3"/>
      <path d="M0 207 Q60 270 230 291 L0 291 Z" fill="var(--peach)"/>
      <path d="M0 207 Q60 270 230 291" fill="none" stroke="var(--maroon)" stroke-width="3"/>
    </svg>

    <h1 class="brand-name">Marlow &amp; Quince</h1>

    <p class="person">Your name, <span class="person__title">Title</span></p>

    <address class="address">Street Name, City Name<br>State Zip Code</address>

    <ul class="contacts">
      <li>
        <svg viewBox="0 0 10 10" aria-hidden="true"><path d="M2 1 L4 1 L4.6 3 L3.4 4 Q4.5 6 6 6.6 L7 5.4 L9 6 L9 8 Q8.5 9 7.5 9 Q1 8 1 2.5 Q1 1.5 2 1 Z" fill="var(--maroon)"/></svg>
        987-654-3210
      </li>
      <li>
        <svg viewBox="0 0 10 10" aria-hidden="true"><rect x="2.5" y="0.5" width="5" height="9" rx="1" fill="var(--maroon)"/><rect x="3.3" y="1.6" width="3.4" height="5" fill="var(--white)"/></svg>
        987-654-3210
      </li>
      <li>
        <svg viewBox="0 0 10 10" aria-hidden="true"><rect x="0.5" y="2" width="9" height="6" fill="var(--maroon)"/><path d="M0.8 2.3 L5 5.5 L9.2 2.3" fill="none" stroke="var(--white)" stroke-width="0.8"/></svg>
        info@marlow&amp;quince.com
      </li>
      <li>
        <svg viewBox="0 0 10 10" aria-hidden="true"><circle cx="5" cy="5" r="4.3" fill="var(--maroon)"/><path d="M0.7 5 H9.3 M5 0.7 V9.3 M5 0.7 Q2.2 5 5 9.3 M5 0.7 Q7.8 5 5 9.3" fill="none" stroke="var(--white)" stroke-width="0.6"/></svg>
        www.marlow&amp;quince.com
      </li>
    </ul>
  </section>

  <section class="card card--back">
    <p class="monogram">M &amp; Q</p>
  </section>

</div>
</body>
</html>
```